Business Card Design Project

Tidal Oak Jobs- http:tidaloakjobs.com./janetpruitt

Industry/Entity Type

Business

Contact Information for Business Card

Well it could be a pretty color like a glossy pink look business type very Job related

```html
<!DOCTYPE html>
<html lang="en">
<head>
<meta charset="utf-8">
<title>Janet Pruitt – Business Card</title>
<link rel="stylesheet" href="https://fonts.googleapis.com/css2?family=Cinzel:wght@400&family=Open+Sans:wght@400&display=swap">
<style>
  :root {
    --backdrop: #2b2622;
    --card: #0b0b0b;
    --card-edge: #1a1a1a;
    --pink: #e8185f;
    --silver: #cfcfcf;
    --text-light: #e6e6e6;
    --icon-line: #bdbdbd;
  }
  html, body {
    margin: 0;
    width: 1200px;
    height: 844px;
    overflow: hidden;
    background: var(--backdrop);
  }
  .stage {
    position: relative;
    width: 1200px;
    height: 844px;
  }
  .card {
    position: absolute;
    width: 520px;
    height: 300px;
    background: radial-gradient(ellipse at 60% 40%, #151515 0%, var(--card) 70%);
    border: 1px solid var(--card-edge);
    box-shadow: 0 10px 30px rgba(0,0,0,0.55);
    box-sizing: border-box;
  }
  .card--contact { left: 50px; top: 272px; }
  .card--brand { left: 630px; top: 272px; }

  .brand-row {
    position: absolute;
    left: 48px;
    top: 78px;
    display: flex;
    align-items: center;
    gap: 18px;
  }
  .brand-square {
    width: 58px;
    height: 48px;
    border: 4px solid var(--pink);
    box-sizing: border-box;
  }
  .holder-name {
    font-family: "Cinzel", serif;
    font-size: 24px;
    letter-spacing: 1px;
    color: var(--text-light);
    margin: 0;
  }

  .contact-list {
    position: absolute;
    left: 48px;
    bottom: 30px;
    margin: 0;
    padding: 0;
    list-style: none;
    font-family: "Open Sans", sans-serif;
    font-size: 14px;
    color: var(--text-light);
    letter-spacing: 0.3px;
  }
  .contact-list li {
    display: flex;
    align-items: center;
    gap: 9px;
    height: 22px;
  }
  .contact-icon {
    width: 17px;
    height: 17px;
    background: var(--pink);
    display: flex;
    align-items: center;
    justify-content: center;
  }

  .social-column {
    position: absolute;
    right: 30px;
    top: 52px;
    display: flex;
    flex-direction: column;
    gap: 8px;
  }
  .social-dot {
    width: 20px;
    height: 20px;
    border: 1.5px solid var(--icon-line);
    border-radius: 50%;
    box-sizing: border-box;
  }

  .brand-center {
    position: absolute;
    left: 0;
    right: 0;
    top: 78px;
    display: flex;
    flex-direction: column;
    align-items: center;
    gap: 22px;
  }
  .brand-square--silver {
    width: 118px;
    height: 88px;
    border: 6px solid var(--silver);
    box-sizing: border-box;
  }
  .holder-name--large {
    font-size: 30px;
    color: var(--silver);
  }
</style>
</head>
<body>
<main class="stage">
  <section class="card card--contact" aria-label="Card back with contact details">
    <div class="brand-row">
      <div class="brand-square" aria-hidden="true"></div>
      <h2 class="holder-name">Janet Pruitt</h2>
    </div>

    <div class="social-column" aria-label="Social profiles">
      <span class="social-dot"></span>
      <span class="social-dot"></span>
      <span class="social-dot"></span>
      <span class="social-dot"></span>
    </div>

    <ul class="contact-list">
      <li>
        <span class="contact-icon">
          <svg width="11" height="11" viewBox="0 0 24 24" aria-hidden="true"><path fill="#fff" d="M6.6 10.8a15 15 0 0 0 6.6 6.6l2.2-2.2c.3-.3.7-.4 1-.2 1.1.4 2.3.6 3.6.6.6 0 1 .4 1 1V20c0 .6-.4 1-1 1A17 17 0 0 1 3 4c0-.6.4-1 1-1h3.5c.6 0 1 .4 1 1 0 1.3.2 2.5.6 3.6.1.3 0 .7-.2 1z"/></svg>
        </span>
        044-555 018 247
      </li>
      <li>
        <span class="contact-icon">
          <svg width="11" height="11" viewBox="0 0 24 24" aria-hidden="true"><path fill="#fff" d="M2 5h20v14H2z"/><path fill="none" stroke="#e8185f" stroke-width="2" d="M2 5l10 8 10-8"/></svg>
        </span>
        INFO@TIDALOAKJOBS.COM
      </li>
      <li>
        <span class="contact-icon">
          <svg width="11" height="11" viewBox="0 0 24 24" aria-hidden="true"><circle cx="12" cy="12" r="9" fill="none" stroke="#fff" stroke-width="2.5"/><path fill="none" stroke="#fff" stroke-width="2" d="M3 12h18M12 3c3 3 3 15 0 18M12 3c-3 3-3 15 0 18"/></svg>
        </span>
        WWW.TIDALOAKJOBS.COM
      </li>
    </ul>
  </section>

  <section class="card card--brand" aria-label="Card front with name">
    <div class="brand-center">
      <div class="brand-square brand-square--silver" aria-hidden="true"></div>
      <h1 class="holder-name holder-name--large">Janet Pruitt</h1>
    </div>
  </section>
</main>
</body>
</html>
```